Home Staging Company needs business card design

We're a home staging company called Brightly Settled Home Staging. We would like a business card design that includes aqua and gray. Our current logo of house within chair is fine but I find we almost always use the logo in one color. I'll upload images of front and back of our current card and our logo. Note that we have dropped "Solutions" from our company name and don't want to include it on the card.

Target Market(s)

Realtors and homeowners - people interested in selling their homes

Contact Information for Business Card

Marisol Thistlewood
Brightly Settled Home Staging
757-555-0193
www.brightlysettled.com
marisol@brightlysettled.com

Font styles to use
Serif
Script

Requirements
Must have
• My logo and contact details
• UPDATE***
• I forgot to say that the company name should be included on the front of the card somehow.

```html
<!DOCTYPE html>
<html lang="en">
<head>
<meta charset="utf-8">
<title>Brightly Settled Home Staging – Business Card</title>
<link rel="stylesheet" href="https://fonts.googleapis.com/css2?family=Playfair+Display:wght@400;600&family=Roboto+Condensed:wght@400&family=Questrial&display=swap">
<style>
  :root {
    --page: #bdbdbd;
    --aqua: #4aa9b2;
    --aqua-light: #55b3ba;
    --aqua-deep: #1f88ad;
    --charcoal: #333638;
    --ink: #3a3a3a;
    --paper-top: #f7f7f7;
    --paper-bottom: #e6e6e6;
    --white: #ffffff;
  }
  * { box-sizing: border-box; margin: 0; padding: 0; }
  html, body { width: 1200px; height: 576px; overflow: hidden; }
  body {
    background: var(--page);
    position: relative;
    font-family: "Questrial", sans-serif;
  }
  .card {
    position: absolute;
    top: 138px;
    width: 484px;
    height: 294px;
    border-radius: 14px;
    overflow: hidden;
  }

  /* Front */
  .card-front {
    left: 82px;
    background: linear-gradient(180deg, var(--aqua-light) 0%, var(--aqua) 40%, var(--aqua-deep) 100%);
    color: var(--white);
    text-align: center;
  }
  .front-name {
    position: absolute;
    left: 0; right: 0;
    top: 106px;
    font-family: "Playfair Display", serif;
    font-weight: 400;
    font-size: 40px;
    line-height: 1.1;
    color: var(--white);
  }
  .front-web {
    position: absolute;
    left: 0; right: 0;
    top: 266px;
    font-size: 14px;
    letter-spacing: 0.2px;
  }

  /* Back */
  .card-back {
    left: 602px;
    background: linear-gradient(180deg, var(--paper-top), var(--paper-bottom));
    color: var(--ink);
  }
  .brand {
    position: absolute;
    left: 22px;
    top: 58px;
    display: flex;
    align-items: center;
    gap: 14px;
  }
  .brand-mark {
    width: 44px;
    height: 44px;
    background: var(--aqua);
  }
  .brand-name {
    font-family: "Playfair Display", serif;
    font-weight: 600;
    font-size: 26px;
    color: var(--ink);
    line-height: 1;
  }
  .person {
    position: absolute;
    left: 26px;
    top: 188px;
  }
  .person-name {
    font-family: "Roboto Condensed", sans-serif;
    font-size: 21px;
    color: var(--ink);
  }
  .person-name .surname { color: var(--aqua); }
  .person-title {
    margin-top: 6px;
    font-size: 12px;
    color: var(--ink);
  }
  .contacts {
    position: absolute;
    left: 254px;
    top: 190px;
    list-style: none;
    font-size: 12.5px;
    color: var(--ink);
  }
  .contacts li {
    display: flex;
    align-items: center;
    gap: 11px;
    height: 17.5px;
  }
  .contacts svg { width: 11px; height: 11px; fill: var(--aqua); flex: none; }
  .band-dark {
    position: absolute;
    left: 0; bottom: 0;
    width: 230px;
    height: 12px;
    background: var(--charcoal);
  }
  .band-cta {
    position: absolute;
    left: 206px; right: 0; bottom: 0;
    height: 36px;
    background: var(--aqua);
    clip-path: polygon(14px 0, 100% 0, 100% 100%, 0 100%);
    color: var(--white);
    font-size: 12.5px;
    display: flex;
    align-items: center;
    padding-left: 48px;
  }
</style>
</head>
<body>

<section class="card card-front" aria-label="Card front">
  <p class="front-name">Brightly Settled<br>Home Staging</p>
  <p class="front-web">www.brightlysettled.com</p>
</section>

<section class="card card-back" aria-label="Card back">
  <div class="brand">
    <span class="brand-mark"></span>
    <span class="brand-name">Brightly Settled Home Staging</span>
  </div>

  <div class="person">
    <p class="person-name">Marisol <span class="surname">Thistlewood</span></p>
    <p class="person-title">Managing Director</p>
  </div>

  <ul class="contacts">
    <li>
      <svg viewBox="0 0 16 16" aria-hidden="true"><path d="M3 1h3l1.5 4-2 1.2a9 9 0 0 0 4.3 4.3L11 8.5l4 1.5v3a2 2 0 0 1-2 2A12 12 0 0 1 1 3a2 2 0 0 1 2-2z"/></svg>
      757-555-0193
    </li>
    <li>
      <svg viewBox="0 0 16 16" aria-hidden="true"><path d="M8 0a8 8 0 1 0 0 16A8 8 0 0 0 8 0zm5.9 7h-2.6a12 12 0 0 0-1-4.6A6 6 0 0 1 13.9 7zM8 2c.8 1 1.3 2.9 1.4 5H6.6C6.7 4.9 7.2 3 8 2zM5.7 2.4A12 12 0 0 0 4.7 7H2.1a6 6 0 0 1 3.6-4.6zM2.1 9h2.6a12 12 0 0 0 1 4.6A6 6 0 0 1 2.1 9zM8 14c-.8-1-1.3-2.9-1.4-5h2.8c-.1 2.1-.6 4-1.4 5zm2.3-.4a12 12 0 0 0 1-4.6h2.6a6 6 0 0 1-3.6 4.6z"/></svg>
      www.brightlysettled.com
    </li>
    <li>
      <svg viewBox="0 0 16 16" aria-hidden="true"><path d="M0 3h16v1.2L8 9 0 4.2z M0 5.6l8 4.8 8-4.8V13H0z"/></svg>
      marisol@brightlysettled.com
    </li>
  </ul>

  <div class="band-dark"></div>
  <div class="band-cta">Schedule a consultation today!</div>
</section>

</body>
</html>
```